Chartered Professional Accounting Firm Needs a Business Card Design

We need a card design for an accounting firm based in Toronto, Ontario. The firm name is Pavel Ostrom Professional Corporation. The owner of the firm is a chartered professional accountant and a certified general accountant. Services of the firm include 60% tax preparation and consulting and 40% financial statements for corporation year-end. We would like a modern design. The color could be black, white, gray, blue or other color to bring more confidence to clients. The logo of the firm should be included in the design. Thanks

Name: Pavel Ostrom, CPA, CGA Address: 47 Maple Crest Rd. Richmond Hill, ON L7K 3B5 Telephone: (416) 562-3907 Fax:(416) 734-2165 Email: pavel@pavelostrom-example.ca

Accounting

```html
<!DOCTYPE html>
<html lang="en">
<head>
<meta charset="utf-8">
<title>Pavel Ostrom Professional Corporation – Business Card</title>
<link rel="stylesheet" href="https://fonts.googleapis.com/css2?family=Cinzel:wght@600;700&family=Montserrat:wght@400;500&display=swap">
<style>
  :root {
    --bg: #e4e4e6;
    --card-white: #ffffff;
    --card-silver: #d9d9dc;
    --brand-blue: #3a3f95;
    --band-light: #4a52a8;
    --band-dark: #1f2480;
    --text-grey: #6f7078;
    --rule-grey: #a9aab0;
    --on-band: #ffffff;
  }
  * { box-sizing: border-box; margin: 0; padding: 0; }
  html, body { width: 1200px; height: 871px; overflow: hidden; }
  body {
    background: var(--bg);
    display: flex;
    align-items: center;
    justify-content: center;
    gap: 44px;
  }
  .card {
    position: relative;
    width: 520px;
    height: 297px;
    border-radius: 3px;
    overflow: hidden;
    box-shadow: 0 10px 28px rgba(0,0,0,0.18);
  }
  .card--front {
    background: linear-gradient(150deg, var(--card-white) 0%, #f1f1f3 45%, var(--card-silver) 100%);
  }
  .card--back { background: var(--card-white); }

  .brand { position: absolute; display: flex; align-items: flex-start; gap: 8px; }
  .brand__mark { width: 34px; height: 34px; background: var(--brand-blue); flex: none; margin-top: 2px; }
  .brand__name {
    font-family: "Cinzel", serif;
    font-weight: 700;
    color: var(--brand-blue);
    line-height: 1;
  }
  .brand__name .firm { display: block; font-size: 23px; letter-spacing: 0.5px; }
  .brand__name .corp { display: block; font-size: 9.6px; letter-spacing: 0.4px; margin-top: 2px; }
  .brand__credentials {
    font-family: "Cinzel", serif;
    font-weight: 600;
    color: var(--text-grey);
    font-size: 7.6px;
    letter-spacing: 0.6px;
    line-height: 1.2;
    margin-top: 2px;
  }
  .card--front .brand { left: 248px; top: 170px; }
  .card--back .brand { left: 34px; top: 20px; }

  .card__art { position: absolute; inset: 0; width: 520px; height: 297px; }

  .holder-name {
    position: absolute;
    right: 28px;
    top: 136px;
    font-family: "Cinzel", serif;
    font-weight: 600;
    font-size: 15px;
    letter-spacing: 3px;
    color: var(--band-dark);
  }
  .address {
    position: absolute;
    left: 34px;
    top: 156px;
    font-family: "Montserrat", sans-serif;
    font-size: 10px;
    letter-spacing: 1.6px;
    line-height: 20px;
    color: var(--on-band);
  }
  .contact-list {
    position: absolute;
    right: 16px;
    top: 214px;
    list-style: none;
    font-family: "Montserrat", sans-serif;
    font-size: 10px;
    letter-spacing: 1.6px;
    color: var(--on-band);
  }
  .contact-list li {
    display: flex;
    justify-content: flex-end;
    align-items: center;
    gap: 12px;
    height: 21px;
  }
  .contact-list svg { width: 13px; height: 13px; flex: none; }
</style>
</head>
<body>

  <section class="card card--front" aria-label="Business card front">
    <div class="brand">
      <span class="brand__mark"></span>
      <div>
        <div class="brand__name">
          <span class="firm">PAVEL OSTROM</span>
          <span class="corp">PROFESSIONAL CORPORATION</span>
        </div>
        <div class="brand__credentials">Chartered Professional Accountant<br>Certified General Accountant</div>
      </div>
    </div>
  </section>

  <section class="card card--back" aria-label="Business card back">
    <svg class="card__art" viewBox="0 0 520 297" aria-hidden="true">
      <defs>
        <linearGradient id="bandFill" x1="0" y1="0" x2="1" y2="1">
          <stop offset="0" stop-color="var(--band-light)"/>
          <stop offset="1" stop-color="var(--band-dark)"/>
        </linearGradient>
      </defs>
      <line x1="40" y1="124" x2="512" y2="192" stroke="var(--rule-grey)" stroke-width="1"/>
      <polygon points="0,138 520,212 520,297 0,297" fill="url(#bandFill)"/>
    </svg>

    <div class="brand">
      <span class="brand__mark"></span>
      <div>
        <div class="brand__name">
          <span class="firm">PAVEL OSTROM</span>
          <span class="corp">PROFESSIONAL CORPORATION</span>
        </div>
        <div class="brand__credentials">Chartered Professional Accountant<br>Certified General Accountant</div>
      </div>
    </div>

    <p class="holder-name">Pavel Ostrom, CPA, CGA</p>

    <p class="address">47 Maple Crest<br>Rd. Richmond Hill<br>ON L7K 3B5</p>

    <ul class="contact-list">
      <li>(416) 562-3907
        <svg viewBox="0 0 16 16" aria-label="Telephone"><path d="M2 5c0-2 2-3 6-3s6 1 6 3v1h-3V4.5C10 4 9 4 8 4s-2 0-3 .5V6H2zM4 7h8l1 6H3z" fill="none" stroke="currentColor" stroke-width="1.2"/><circle cx="8" cy="10" r="1.5" fill="currentColor"/></svg>
      </li>
      <li>(416) 734-2165
        <svg viewBox="0 0 16 16" aria-label="Fax"><rect x="4" y="2" width="8" height="4" fill="none" stroke="currentColor" stroke-width="1.2"/><rect x="2" y="6" width="12" height="6" rx="1" fill="none" stroke="currentColor" stroke-width="1.2"/><rect x="4.5" y="10" width="7" height="4" fill="none" stroke="currentColor" stroke-width="1.2"/></svg>
      </li>
      <li>pavel@pavelostrom-example.ca
        <svg viewBox="0 0 16 16" aria-label="Email"><rect x="1.5" y="3.5" width="13" height="9" fill="none" stroke="currentColor" stroke-width="1.2"/><path d="M1.5 3.5 8 9l6.5-5.5" fill="none" stroke="currentColor" stroke-width="1.2"/></svg>
      </li>
    </ul>
  </section>

</body>
</html>
```